Non fiction leadership Book Cover design needed for “Stay Bold: Build On Lasting Discipline”

I need a front cover design for a new book 6 X 9 traditional non-fiction book.

Title: "Stay BOLD - Build On Lasting Discipline"

The subtitle is not finalized- so use 2 lines of smaller dummy text

My brand guide is attached (please use the tan color sparingly)

I'd like to see BOLD look like it is in motion and "flying" across the page

Need CREATIVE designs and options

Do not want my picture on the front cover - I do want it on the back cover.

On the front cover I’d like to see creative use of font to create movement on “BOLD”

Target Market(s)

Business leaders

Industry/Entity Type

Aviation

Font styles to use
Other font styles liked:
• See style guide- can add additional font (modern script or san serif)

Colors
0054AA
0677BA
7BADD7
CADEEF
E8F1F8
EB3D1F
EC4F4E
F09395
F8D3D4
FCEDEE

Requirements
Must have
• Creative font use, using perspective to create movement/motion on BOLD
Should not have
• My picture on the front cover- my picture should be on the back cover

```html
<!DOCTYPE html>
<html lang="en">
<head>
<meta charset="utf-8">
<title>Stay Bold: Build On Lasting Discipline</title>
<link rel="stylesheet" href="https://fonts.googleapis.com/css2?family=Archivo+Black&family=Roboto+Condensed:wght@700;800&family=Montserrat:wght@700&family=Nunito+Sans:wght@400&display=swap">
<style>
  :root {
    --navy: #0d1333;
    --red: #be1e2d;
    --white: #ffffff;
    --tan-dark: #985a2c;
    --tan-mid: #c48a52;
    --tan-light: #ebc08e;
    --tan-gradient: linear-gradient(90deg, var(--tan-dark), var(--tan-mid) 45%, var(--tan-light));
  }
  * { margin: 0; padding: 0; box-sizing: border-box; }
  html, body { width: 800px; height: 1200px; overflow: hidden; background: var(--white); }
  .cover { position: relative; width: 800px; height: 1200px; overflow: hidden; background: var(--white); }
  .sky-shape { position: absolute; inset: 0; width: 800px; height: 1200px; }

  .artwork-slot {
    position: absolute; left: 540px; top: 86px; width: 220px; height: 166px;
    border-radius: 14px;
    background: linear-gradient(135deg, var(--tan-dark), var(--tan-mid) 55%, var(--tan-light));
  }

  .title-lead {
    position: absolute; left: 160px; top: 278px;
    font-family: "Archivo Black", sans-serif; font-size: 76px; line-height: 1;
    color: var(--red); letter-spacing: -1px;
  }
  .title-word {
    position: absolute; left: 80px; top: 317px;
    font-family: "Archivo Black", sans-serif; font-size: 220px; line-height: 1;
    letter-spacing: -6px; white-space: nowrap;
    background: var(--tan-gradient); -webkit-background-clip: text; background-clip: text;
    color: transparent; transform: scaleX(0.64) skewX(-8deg); transform-origin: left bottom;
  }
  .title-expansion {
    position: absolute; left: 82px; top: 520px;
    font-family: "Roboto Condensed", sans-serif; font-weight: 800; font-size: 34px; line-height: 1;
    color: var(--navy); white-space: nowrap;
  }

  .subtitle-block { position: absolute; left: 74px; top: 722px; width: 470px; }
  .subtitle {
    font-family: "Roboto Condensed", sans-serif; font-weight: 700; font-size: 58px;
    line-height: 0.95; color: var(--red);
  }
  .secondary-title {
    font-family: "Montserrat", sans-serif; font-weight: 700; font-size: 22px;
    color: var(--navy); margin-top: 6px;
  }
  .body-copy {
    font-family: "Nunito Sans", sans-serif; font-size: 21px; line-height: 28px;
    color: var(--navy); margin-top: 16px;
  }

  .author-row { position: absolute; left: 0; right: 0; top: 1088px; height: 47px; }
  .author-bar { position: absolute; top: 0; height: 47px; background: var(--tan-gradient); }
  .author-bar--left { left: 0; width: 42px; }
  .author-bar--right { left: 606px; width: 194px; }
  .author-name {
    position: absolute; left: 70px; top: 0; line-height: 47px;
    font-family: "Montserrat", sans-serif; font-weight: 700; font-size: 36px;
    letter-spacing: 0.33em; color: var(--navy); white-space: nowrap;
  }
</style>
</head>
<body>
<main class="cover">
  <svg class="sky-shape" viewBox="0 0 800 1200" aria-hidden="true">
    <path fill="#0d1333" d="M20 0 C90 110 260 225 430 225 C500 225 560 210 600 195 C570 260 560 330 566 400 C580 560 680 700 800 800 L800 0 Z"/>
  </svg>

  <div class="artwork-slot" role="img" aria-label="Paper plane illustration in tan and red, flying toward the upper right"></div>

  <h1>
    <span class="title-lead">STAY</span>
    <span class="title-word">BOLD</span>
  </h1>
  <p class="title-expansion">BUILD ON LASTING DISCIPLINE</p>

  <section class="subtitle-block">
    <h2 class="subtitle">SUBTITLE<br>PLACEHOLDER</h2>
    <p class="secondary-title">Smaller Secondary Title Placeholder</p>
    <p class="body-copy">Nunito Sans Font Family for All Body Copy -<br>Lorem ipsum dolor sit amet,<br>consectetur adipiscing elit.</p>
  </section>

  <footer class="author-row">
    <span class="author-bar author-bar--left"></span>
    <p class="author-name">Margaret Ellison</p>
    <span class="author-bar author-bar--right"></span>
  </footer>
</main>
</body>
</html>
```